I want ideas sample designs for my book cover

Hello,

We need a book cover designed in flat and 3D Versions. We would like to have jpg and png for final output and include a copy of the PSD for future revisions.

Here are the basic details:

Title: The Harvest of Quiet Builders
Author: Norman Quillfeather

Dimensions of book:

Was looking at the Pavo website for dimensions. I thought you may want to go on there and look at the different sizes. I used the 6x9” perfect bound US trade size for my book. You will see that this has a spine width of 0.225”, Cover size of 12.48 x 9.25” and spine begins at 6.125”

If you need background info on the author just to get an idea what he does, please check:

http://NormanQuillfeather.example

IMPORTANT: Please see attached document for a more detailed info:

Exact Title Of book
Back Cover
Spine Info
Measurements of book and dimension
Examples of book covers
Norman's photo attached

Thanks,
Darlene

Industry/Entity Type

Life Coaching

Font styles to use
Serif

Requirements
Must have
• Jpg, png and PSD files
• title
• author
• exact dimensions
• front and back cover
• flat and 3d versions

```html
<!DOCTYPE html>
<html lang="en">
<head>
<meta charset="utf-8">
<title>The Harvest of Quiet Builders — Book Cover</title>
<link rel="stylesheet" href="https://fonts.googleapis.com/css2?family=Raleway:wght@200;300;600&family=Roboto+Slab:wght@300;400;700&family=Playfair+Display:ital@1&display=swap">
<style>
  :root {
    --magenta: #ad1a6c;
    --magenta-deep: #92125a;
    --band-dark: #2a1a3c;
    --band-mid: #4b2150;
    --ink-dark: #2c1f38;
    --paper: #ffffff;
    --stage: #f4f4f4;
    --photo-light: #eef1f3;
    --photo-mid: #c9cfd4;
    --copy-light: #f3d6e6;
  }
  * { box-sizing: border-box; margin: 0; padding: 0; }
  html, body { width: 1200px; height: 850px; overflow: hidden; }
  body { background: var(--stage); position: relative; font-family: "Roboto Slab", serif; }

  .cover-wrap {
    position: absolute; left: 131px; top: 80px;
    width: 937px; height: 690px; display: flex;
    box-shadow: 0 10px 30px rgba(0,0,0,.15);
  }

  /* Back cover */
  .back-cover { position: relative; width: 460px; height: 690px; background: var(--magenta); overflow: hidden; }
  .back-copy { position: absolute; left: 22px; top: 26px; width: 416px; color: var(--copy-light);
    font: 300 9.6px/1.5 "Roboto Slab", serif; text-align: justify; }
  .back-copy p { margin-bottom: 11px; }
  .author-band { position: absolute; left: 0; top: 505px; width: 460px; height: 74px;
    background: linear-gradient(90deg, var(--band-mid), var(--band-dark)); }
  .author-photo { position: absolute; left: 22px; top: 478px; width: 146px; height: 128px;
    border: 4px solid var(--paper); border-radius: 10px;
    background: linear-gradient(135deg, #d9d9d9, #6e6e6e); }
  .author-name { position: absolute; left: 190px; top: 512px; color: var(--paper);
    font: 400 24px/1.05 "Roboto Slab", serif; text-transform: uppercase; letter-spacing: .5px; }
  .author-site { position: absolute; left: 190px; top: 560px; color: var(--paper);
    font: 400 11px "Roboto Slab", serif; }
  .author-mark { position: absolute; left: 70px; top: 628px; display: flex; align-items: center; gap: 8px;
    color: var(--paper); font: 400 18px "Roboto Slab", serif; }
  .author-mark .dot { width: 14px; height: 14px; border-radius: 50%; background: var(--paper); }

  /* Spine */
  .spine { width: 17px; height: 690px; background: var(--magenta-deep); position: relative; }
  .spine-title { position: absolute; left: 50%; top: 50%; transform: translate(-50%, -50%) rotate(90deg);
    white-space: nowrap; color: var(--paper); font: 400 9px "Roboto Slab", serif; letter-spacing: 2px; text-transform: uppercase; }

  /* Front cover */
  .front-cover { position: relative; width: 460px; height: 690px; background: var(--magenta); overflow: hidden; }
  .front-shapes { position: absolute; inset: 0; }
  .title { position: absolute; left: 22px; top: 352px; color: var(--paper); }
  .title-lead { font: 600 58px/1 "Raleway", sans-serif; letter-spacing: -1px; }
  .title-middle { font: 200 44px/1 "Raleway", sans-serif; margin-top: -2px; }
  .title-key { font: 700 50px/1 "Roboto Slab", serif; color: var(--ink-dark); letter-spacing: 1px; margin-top: 2px; }
  .subtitle-band { position: absolute; left: 0; top: 520px; width: 460px; height: 64px;
    background: linear-gradient(90deg, var(--band-dark), var(--band-mid)); }
  .subtitle { position: absolute; left: 22px; top: 526px; width: 420px; color: var(--paper);
    font: 300 12.5px/1.35 "Roboto Slab", serif; }
  .byline-lead { position: absolute; left: 22px; top: 604px; color: var(--paper); font: 300 16px "Roboto Slab", serif; }
  .byline-lead strong { font-weight: 700; }
  .byline-author { position: absolute; left: 22px; top: 628px; color: var(--ink-dark);
    font: italic 22px "Playfair Display", serif; }
</style>
</head>
<body>
  <main class="cover-wrap">
    <section class="back-cover" aria-label="Back cover">
      <div class="back-copy">
        <p>This book goes far beyond business. It is a book for the awakening builder whose work is shaping a better world for the generations still to come. It brings you a fresh, grounded way of working from the inside out, so your company can move with clarity towards its vision, mission and purpose.</p>
        <p>You have the power to lead a fuller life and run a kinder business by seeing the quiet ties between all living things. This book will help you take your life and work to the next level, and show you how slow, patient practice can heal the bonds with yourself, your partner, your family and your team.</p>
        <p>Norman shares his own heartfelt stories and the lessons he gathered from years among growers, makers and elders who keep old ways alive. He has turned himself inside out to change his own life and business, and he wants to help you do the same. When enough of us take this journey, together we can leave a lasting mark.</p>
        <p>Norman Quillfeather is a widely known entrepreneur, speaker, coach and best-selling author. Having worked with people in more than twenty countries, he now invites you to look deep within yourself and explore your true nature. Many leaders say Norman's gift is to blend purpose with profit in a way that brings meaning to their daily work.</p>
      </div>
      <div class="author-band"></div>
      <div class="author-photo" role="img" aria-label="Black and white portrait photo of the author"></div>
      <div class="author-name">Norman<br>Quillfeather</div>
      <div class="author-site">www.NormanQuillfeather.example</div>
      <div class="author-mark"><span class="dot"></span>NQ</div>
    </section>

    <section class="spine" aria-label="Spine">
      <div class="spine-title">The Harvest of Quiet Builders</div>
    </section>

    <section class="front-cover" aria-label="Front cover">
      <svg class="front-shapes" width="460" height="690" viewBox="0 0 460 690">
        <defs>
          <linearGradient id="photoTone" x1="0" y1="0" x2="0" y2="1">
            <stop offset="0" stop-color="#f4f6f8"/>
            <stop offset="1" stop-color="#c4cad0"/>
          </linearGradient>
        </defs>
        <rect x="12" y="14" width="130" height="250" fill="#bd3a82" opacity=".55"
              role="img" aria-label="Line drawings of scattered light bulbs"/>
        <polygon points="240,0 460,0 460,330 250,330 130,165" fill="var(--paper)"/>
        <polygon points="250,20 446,20 446,318 258,318 150,165" fill="url(#photoTone)"
                 role="img" aria-label="Photo of a man in a suit standing inside a glowing light bulb"/>
        <polygon points="392,330 460,290 460,420" fill="#3a3050"/>
        <polygon points="300,690 460,690 460,560" fill="#9c1662" opacity=".6"/>
        <path d="M386,690 Q400,640 460,612 L460,690 Z" fill="var(--paper)"/>
      </svg>
      <div class="title">
        <div class="title-lead">the</div>
        <div class="title-middle">harvest of quiet</div>
        <div class="title-key">BUILDERS</div>
      </div>
      <div class="subtitle-band"></div>
      <p class="subtitle">How this ancient wisdom is helping billionaires, industry icons and entrepreneurs to be better leaders, increase impact and leave a legacy.</p>
      <p class="byline-lead">From the Best Selling Author of <strong>“UNDERTOW”</strong></p>
      <p class="byline-author">Norman Quillfeather</p>
    </section>
  </main>
</body>
</html>
```